Income Tax Flyer - Updates Needed

Just need to update this flyer design and give it a new look. We would like to keep all the same wording but make it stand out a little more. Our selling point is the "Same Day Tax Advance up to $6,000"

Lending, Small Loans, Tax Services, Title Loans, Personal Loans

```html
<!DOCTYPE html>
<html lang="en">
<head>
<meta charset="utf-8">
<title>Northvale Financial Group – Same Day Tax Advance</title>
<link rel="stylesheet" href="https://fonts.googleapis.com/css2?family=Archivo+Black&family=EB+Garamond:wght@700&family=Libre+Baskerville:wght@700&family=Poppins:wght@400&family=Sorts+Mill+Goudy&display=swap">
<style>
  :root {
    --green: #12502e;
    --green-dark: #0e4426;
    --red: #c21f26;
    --paper: #f3f3f3;
    --white: #ffffff;
    --blush: rgba(194, 31, 38, 0.09);
  }
  html, body {
    margin: 0;
    padding: 0;
    overflow: hidden;
    background: var(--white);
  }
  .flyer {
    position: relative;
    width: 909px;
    height: 1200px;
    overflow: hidden;
    background:
      linear-gradient(125deg, rgba(255,255,255,0) 20%, rgba(255,255,255,0.9) 30%, rgba(255,255,255,0) 42%),
      linear-gradient(160deg, #ececec 0%, #f7f7f7 40%, var(--paper) 100%);
    font-family: "Libre Baskerville", Georgia, serif;
    color: var(--green);
  }
  .abs { position: absolute; }

  /* brand */
  .brand {
    left: 40px;
    top: 30px;
    width: 220px;
    text-align: center;
    font-family: "Libre Baskerville", Georgia, serif;
    font-weight: 700;
    color: var(--green);
    line-height: 1.1;
  }
  .brand-name { font-size: 30px; letter-spacing: -0.5px; display: block; }
  .brand-sub { font-size: 10px; letter-spacing: 3px; display: block; margin-top: 6px; }

  .tagline {
    left: 328px;
    top: 48px;
    font-size: 22px;
    letter-spacing: -0.6px;
    white-space: nowrap;
    margin: 0;
  }
  .tagline .amount {
    font-family: "Archivo Black", Arial, sans-serif;
    color: var(--red);
    font-size: 26px;
    letter-spacing: 0;
  }

  .dot-grid { left: 4px; top: 161px; }

  .hero-photo {
    left: 580px;
    top: 106px;
    width: 490px;
    height: 490px;
    border-radius: 50%;
    border: 3px solid var(--white);
    box-sizing: border-box;
    background: radial-gradient(circle at 42% 40%, #d9c4b6 0%, #9a8a84 28%, #6f7b86 55%, #3b4652 100%);
  }

  /* headline */
  .headline { left: 73px; top: 236px; margin: 0; font-weight: 700; }
  .headline-line {
    display: block;
    font-size: 50px;
    letter-spacing: -2px;
    line-height: 1;
  }
  .amount-band {
    left: 68px;
    top: 289px;
    width: 461px;
    height: 84px;
    background: var(--red);
    transform: skewY(-0.6deg);
  }
  .amount-range {
    left: 73px;
    top: 297px;
    font-family: "Archivo Black", Arial, sans-serif;
    font-size: 56px;
    color: var(--white);
    letter-spacing: -1px;
    white-space: nowrap;
    text-shadow: 3px 3px 0 var(--green);
    line-height: 1.2;
  }
  .today { left: 73px; top: 378px; }

  .subhead {
    left: 73px;
    top: 478px;
    margin: 0;
    font-family: "EB Garamond", Georgia, serif;
    font-weight: 700;
    font-size: 31px;
    letter-spacing: 2.4px;
    color: var(--red);
    white-space: nowrap;
  }
  .subhead-strong {
    left: 73px;
    top: 528px;
    margin: 0;
    font-size: 40px;
    letter-spacing: -1.8px;
    white-space: nowrap;
  }

  /* lower art */
  .lower-art { left: 0; top: 0; }

  /* features */
  .features { left: 74px; top: 628px; margin: 0; padding: 0; list-style: none; }
  .feature {
    position: relative;
    height: 68px;
    margin-bottom: 22px;
    display: flex;
    align-items: center;
  }
  .feature-icon {
    width: 68px;
    height: 68px;
    border-radius: 50%;
    background: var(--green);
    display: flex;
    align-items: center;
    justify-content: center;
    flex: none;
    position: relative;
    z-index: 1;
  }
  .feature-label {
    margin-left: 8px;
    height: 52px;
    width: 272px;
    padding-left: 8px;
    display: flex;
    align-items: center;
    background: linear-gradient(90deg, var(--blush) 0%, var(--blush) 70%, rgba(194,31,38,0) 100%);
    font-family: "Sorts Mill Goudy", Georgia, serif;
    font-size: 20px;
    color: var(--green);
    white-space: nowrap;
  }

  /* footer */
  .footer {
    left: 0;
    top: 1066px;
    width: 909px;
    height: 134px;
    background: var(--green-dark);
    color: var(--white);
  }
  .footer-cta {
    position: absolute;
    left: 48px;
    top: 46px;
    margin: 0;
    font-size: 31px;
    letter-spacing: -1px;
  }
  .footer-divider {
    position: absolute;
    left: 447px;
    top: 22px;
    width: 1px;
    height: 100px;
    background: rgba(255,255,255,0.7);
  }
  .footer-phone {
    position: absolute;
    left: 476px;
    top: 36px;
    margin: 0;
    font-size: 30px;
    letter-spacing: -1px;
  }
  .footer-address {
    position: absolute;
    left: 476px;
    top: 88px;
    display: flex;
    gap: 36px;
    font-family: "Poppins", Arial, sans-serif;
    font-size: 14px;
    margin: 0;
    font-style: normal;
  }
  .footer-code {
    position: absolute;
    right: 14px;
    bottom: 8px;
    font-family: "Poppins", Arial, sans-serif;
    font-size: 9px;
  }
  .footer-dots { position: absolute; left: 2px; top: 92px; }
</style>
</head>
<body>
<main class="flyer">

  <!-- corner stripe -->
  <svg class="abs" style="left:0;top:0" width="909" height="140" viewBox="0 0 909 140" aria-hidden="true">
    <path d="M896 0 L909 0 L909 128 L885 118 Z" fill="var(--red)"/>
  </svg>

  <div class="abs brand">
    <span class="brand-name">Northvale</span>
    <span class="brand-sub">FINANCIAL GROUP</span>
  </div>

  <h2 class="abs tagline">SAME DAY TAX ADVANCE UP TO <span class="amount">$6,000</span></h2>

  <svg class="abs dot-grid" width="34" height="60" viewBox="0 0 34 60" aria-hidden="true">
    <g fill="#cfcfcf">
      <circle cx="2" cy="2" r="2"/><circle cx="16" cy="2" r="2"/><circle cx="30" cy="2" r="2"/>
      <circle cx="2" cy="16" r="2"/><circle cx="16" cy="16" r="2"/><circle cx="30" cy="16" r="2"/>
      <circle cx="2" cy="30" r="2"/><circle cx="16" cy="30" r="2"/><circle cx="30" cy="30" r="2"/>
      <circle cx="2" cy="44" r="2"/><circle cx="16" cy="44" r="2"/><circle cx="30" cy="44" r="2"/>
      <circle cx="2" cy="58" r="2"/><circle cx="16" cy="58" r="2"/><circle cx="30" cy="58" r="2"/>
    </g>
  </svg>

  <div class="abs hero-photo" role="img" aria-label="Smiling businesswoman in a grey blazer shaking hands in an office"></div>

  <!-- lower photo band with red swooshes -->
  <svg class="abs lower-art" width="909" height="1066" viewBox="0 0 909 1066">
    <defs>
      <linearGradient id="officeTone" x1="0" y1="0" x2="1" y2="1">
        <stop offset="0" stop-color="#dfe7e1"/>
        <stop offset="0.5" stop-color="#b9c8bf"/>
        <stop offset="1" stop-color="#6f7f76"/>
      </linearGradient>
    </defs>
    <path role="img" aria-label="Smiling businesswoman and businessman looking at documents together in a bright office"
          d="M0 1012 Q 470 930 748 597 L909 585 L909 1058 L0 1058 Z" fill="url(#officeTone)"/>
    <path d="M0 998 Q 450 915 678 563 L712 582 Q 470 930 0 1012 Z" fill="var(--red)"/>
    <path d="M0 1012 Q 470 930 712 582 L748 597 Q 480 950 0 1020 Z" fill="var(--white)"/>
    <path d="M909 895 L909 915 L770 1058 L746 1058 Z" fill="var(--red)"/>
    <path d="M909 915 L909 1058 L770 1058 Z" fill="var(--white)"/>
  </svg>

  <h1 class="abs headline">
    <span class="headline-line">APPLY HERE FOR</span>
  </h1>
  <div class="abs amount-band"></div>
  <div class="abs amount-range">$ 5,000–$6,000</div>
  <div class="abs headline today"><span class="headline-line">TODAY !</span></div>

  <p class="abs subhead">File your taxes &amp; apply for an</p>
  <p class="abs headline subhead-strong">EASY ADVANCE!</p>

  <ul class="abs features">
    <li class="feature">
      <span class="feature-icon">
        <svg width="40" height="40" viewBox="0 0 40 40" fill="none" stroke="#fff" stroke-width="1.6" aria-hidden="true">
          <circle cx="20" cy="20" r="16"/><circle cx="20" cy="20" r="12"/>
          <path d="M20 12 V20 L26 16" stroke-linecap="round"/>
          <path d="M32 6 L34 11 L29 11"/>
        </svg>
      </span>
      <span class="feature-label">Available in 24 Hours or Less</span>
    </li>
    <li class="feature">
      <span class="feature-icon">
        <svg width="42" height="42" viewBox="0 0 42 42" fill="none" stroke="#fff" stroke-width="1.6" aria-hidden="true">
          <path d="M14 18 L26 8 L38 18 V28 H16"/>
          <circle cx="26" cy="19" r="5"/>
          <path d="M4 28 H12 L20 32 H30 L36 28 M4 28 V36 H12 L22 38 L38 30"/>
        </svg>
      </span>
      <span class="feature-label">Choose your Loan Amount</span>
    </li>
    <li class="feature">
      <span class="feature-icon">
        <svg width="44" height="44" viewBox="0 0 44 44" fill="none" stroke="#fff" stroke-width="1.6" aria-hidden="true">
          <circle cx="26" cy="25" r="13"/><circle cx="26" cy="25" r="9"/>
          <path d="M26 18 V25 L31 28" stroke-linecap="round"/>
          <path d="M23 9 H29 M26 9 V12 M34 11 L37 14"/>
          <path d="M3 20 H11 M5 26 H12 M3 32 H11"/>
        </svg>
      </span>
      <span class="feature-label">Quick &amp; Easy</span>
    </li>
  </ul>

  <footer class="abs footer">
    <h3 class="footer-cta">CONTACT US TODAY!</h3>
    <div class="footer-divider"></div>
    <h3 class="footer-phone">PHONE NUMBER</h3>
    <address class="footer-address">
      <span>Address Line 1</span>
      <span>Address Line 2</span>
      <span>Address Line 3</span>
    </address>
    <span class="footer-code">C64</span>
    <svg class="footer-dots" width="46" height="40" viewBox="0 0 46 40" aria-hidden="true">
      <g fill="rgba(255,255,255,0.25)">
        <circle cx="3" cy="3" r="2"/><circle cx="16" cy="3" r="2"/><circle cx="29" cy="3" r="2"/><circle cx="42" cy="3" r="2"/>
        <circle cx="3" cy="16" r="2"/><circle cx="16" cy="16" r="2"/><circle cx="29" cy="16" r="2"/><circle cx="42" cy="16" r="2"/>
        <circle cx="3" cy="29" r="2"/><circle cx="16" cy="29" r="2"/><circle cx="29" cy="29" r="2"/><circle cx="42" cy="29" r="2"/>
      </g>
    </svg>
  </footer>

</main>
</body>
</html>
```